Lantern Hollow Brewing Company New Website with Food Ordering

We need a wordpress-based website for a local brewery & pizza kitchen. The final design will have 6 primary pages: home page, order pizza, our beers, visit us, about us, merch store. The website must integrate with tillpoint for kitchens for online ordering for takeout and delivery. It will also a feature a selection of beers and help customers navigate to the brewery and find hours of operation. The existing website is lanternhollowbrew.example. This is a very old website.

Industry/Entity Type

Brewery and food service

Coding

Coded - Design and coding required

Number of Pages Required

5+ page

Font styles to use
Sans Serif

Requirements
Must have
• ability to integrate seamlessly with tillpoint for kitchens, 21+ age gate
Nice to have
• see attached pdf

```html
<!DOCTYPE html>
<html lang="en">
<head>
<meta charset="utf-8">
<title>Lantern Hollow Brewing Company</title>
<link rel="stylesheet" href="https://fonts.googleapis.com/css2?family=Open+Sans:wght@400;600;700;800&display=swap">
<style>
:root{
  --red:#c8102e;
  --red-dark:#a30c24;
  --ink:#222222;
  --text:#333333;
  --white:#ffffff;
  --footer:#242424;
  --slate:#2b2b2b;
}
*{box-sizing:border-box;margin:0;padding:0}
html,body{width:1200px;height:2469px;overflow:hidden;background:var(--white)}
body{position:relative;font-family:"Open Sans",Arial,sans-serif;color:var(--text)}
.abs{position:absolute}

/* header */
.brand{left:99px;top:18px;width:120px;display:flex;align-items:center;gap:8px}
.brand-square{width:14px;height:14px;background:var(--red);flex:none}
.brand-name{font-weight:800;font-size:15px;line-height:17px;color:var(--red);text-transform:uppercase}
.main-nav{top:30px;left:0;width:1200px;height:24px}
.main-nav a{position:absolute;font-size:17px;color:var(--ink);text-decoration:none;white-space:nowrap}
.promo-badge{left:1019px;top:6px;width:80px;height:80px;border-radius:50%;background:radial-gradient(circle at 40% 35%,#f03a2a,var(--red) 70%);display:flex;align-items:center;justify-content:center;color:var(--white);font-weight:700;font-size:13px;transform:rotate(-25deg)}

/* hero */
.hero-shape{left:0;top:0}
.hero-title{left:100px;top:228px;font-weight:800;font-size:57px;line-height:67px;color:var(--white);text-transform:uppercase;letter-spacing:.5px}

/* hex buttons */
.hex{position:absolute;height:46px;clip-path:polygon(0 18%,50% 0,100% 18%,100% 82%,50% 100%,0 82%);padding:2px}
.hex span{display:flex;align-items:center;justify-content:center;width:100%;height:100%;clip-path:polygon(0 18%,50% 0,100% 18%,100% 82%,50% 100%,0 82%);font-size:15px;font-weight:600;text-transform:uppercase;white-space:nowrap}
.hex.solid{background:var(--ink)}
.hex.solid span{background:var(--red);color:var(--white)}
.hex.outline{background:var(--ink)}
.hex.outline span{background:var(--white);color:var(--ink)}
.hex.on-hero.outline{background:var(--red)}

/* content sections */
.rule{height:2px;width:45px;background:var(--ink)}
.section-title{font-weight:800;font-size:35px;line-height:43px;color:var(--red);text-transform:uppercase}
.body-copy{font-size:15.5px;line-height:25.7px;color:var(--text)}
.photo{border-radius:90px 10px 90px 10px}
.photo-pizza-top{left:641px;top:780px;width:459px;height:346px;border-radius:90px;background:radial-gradient(circle at 40% 40%,#d98a3a,#a8321c 55%,#5a1a10)}
.photo-pizza-pan{left:100px;top:1600px;width:458px;height:345px;border-radius:90px;background:linear-gradient(135deg,#2a2a2a 0%,#d9a15a 40%,#e0b870 60%,#262626 100%)}
.photo-cans{left:0;top:1787px;width:198px;height:244px;border-radius:6px;background:linear-gradient(90deg,#7bc7d0,#e8c4d8 45%,#6fb75a)}
.sketch-mug{left:14px;top:1126px;width:111px;height:137px;background:#e4e4e4;border-radius:10px}
.sketch-hops{left:1054px;top:1480px;width:139px;height:149px;background:#e4e4e4;border-radius:50%}

.call-title{left:0;width:1200px;top:1258px;text-align:center;font-weight:800;font-size:34px;color:var(--white);text-transform:uppercase}
.call-copy{left:140px;width:920px;top:1327px;text-align:center;font-size:15.5px;line-height:25.7px;color:#e8e8e8}

/* footer */
.footer-name{left:450px;width:300px;top:2172px;text-align:center;font-weight:800;font-size:22px;line-height:28px;color:var(--white);text-transform:uppercase}
.footer-address{left:100px;top:2214px;font-size:17px;line-height:26px;color:var(--white)}
.footer-address .line{display:flex;align-items:center;gap:8px}
.footer-address .indent{padding-left:0}
.footer-phone{left:862px;top:2222px;font-size:20px;color:var(--white);display:flex;align-items:center;gap:12px}
.footer-nav{top:2306px;left:0;width:1200px}
.footer-nav a{position:absolute;font-size:17px;font-weight:600;color:var(--white);text-decoration:none;text-transform:uppercase;white-space:nowrap}
.footer-rule{left:99px;top:2374px;width:1002px;height:1px;background:#8a8a8a}
.copyright{left:92px;top:2399px;font-size:14.5px;color:var(--white)}
.social{left:854px;top:2397px;display:flex;align-items:center;gap:14px;font-size:16px;color:var(--white)}
.social i{display:block;width:17px;height:17px;border-radius:50%;background:var(--white)}
</style>
</head>
<body>

<!-- header -->
<header>
  <div class="abs brand"><span class="brand-square"></span><span class="brand-name">Lantern<br>Hollow</span></div>
  <nav class="abs main-nav">
    <a style="left:393px">The Kitchen</a>
    <a style="left:539px">Our Beers</a>
    <a style="left:671px">Visit Us</a>
    <a style="left:781px">About Us</a>
    <a style="left:905px">Merch</a>
  </nav>
  <div class="abs promo-badge">Try Brightside!</div>
</header>

<!-- hero -->
<svg class="abs hero-shape" width="1200" height="720" viewBox="0 0 1200 720">
  <defs>
    <linearGradient id="heroFill" x1="0" y1="0" x2="1" y2="1">
      <stop offset="0" stop-color="#5a2a1a"/>
      <stop offset=".45" stop-color="#8c4a28"/>
      <stop offset=".75" stop-color="#b8782f"/>
      <stop offset="1" stop-color="#3a2a22"/>
    </linearGradient>
  </defs>
  <polygon points="0,120 585,93 616,93 1200,120 1200,662 616,702 585,702 0,662" fill="url(#heroFill)" role="img" aria-label="Photo of square pizza with a glass of beer and a can"/>
  <polygon points="0,108 585,78 585,92 0,122" fill="var(--red)"/>
  <polygon points="616,78 1200,108 1200,122 616,92" fill="var(--red)"/>
  <polygon points="0,662 585,702 585,717 0,677" fill="var(--red)"/>
  <polygon points="616,702 1200,662 1200,677 616,717" fill="var(--red)"/>
</svg>
<h1 class="abs hero-title">Square pizza and<br>great beer in<br>Portland Maine</h1>
<a class="hex solid" style="left:105px;top:457px;width:139px"><span>Order Pizza</span></a>
<a class="hex outline on-hero" style="left:266px;top:457px;width:139px"><span>Visit Us</span></a>
<a class="hex outline on-hero" style="left:426px;top:457px;width:139px"><span>Our Beers</span></a>
<a class="hex outline on-hero" style="left:586px;top:457px;width:139px"><span>About Us</span></a>

<!-- order pizza -->
<section>
  <div class="abs rule" style="left:100px;top:806px"></div>
  <h2 class="abs section-title" style="left:100px;top:814px">Order Pizza</h2>
  <p class="abs body-copy" style="left:100px;top:871px;width:475px">Lorem ipsum dolor sit amet, consectetur adipiscing elit, sed do eiusmod tempor incididunt ut labore et dolore magna aliqua. Ut enim ad minim veniam, quis nostrud exercitation ullamco laboris nisi ut aliquip ex ea commodo consequat. Duis aute irure dolor in reprehenderit in voluptate velit esse cillum dolore eu fugiat nulla pariatur.</p>
  <a class="hex solid" style="left:100px;top:1048px;width:169px"><span>Order Carryout</span></a>
  <a class="hex outline" style="left:281px;top:1048px;width:169px"><span>Order Delivery</span></a>
  <div class="abs photo-pizza-top" role="img" aria-label="Photo of a pepperoni Detroit-style pizza on a cooling rack"></div>
</section>

<div class="abs sketch-mug" role="img" aria-label="Sketch of a wooden beer mug"></div>

<!-- call band -->
<section>
  <svg class="abs" style="left:0;top:1160px" width="1200" height="400" viewBox="0 1160 1200 400">
    <defs>
      <linearGradient id="slateFill" x1="0" y1="0" x2="0" y2="1">
        <stop offset="0" stop-color="#4a4a4a"/>
        <stop offset=".5" stop-color="#2b2b2b"/>
        <stop offset="1" stop-color="#1c1c1c"/>
      </linearGradient>
    </defs>
    <polygon points="0,1245 605,1164 1200,1231 1200,1485 605,1554 0,1490" fill="url(#slateFill)" role="img" aria-label="Dark wood tabletop with hops and beer glasses"/>
  </svg>
  <h2 class="abs call-title">Questions? Give us a call</h2>
  <p class="abs call-copy">Lorem ipsum dolor sit amet, consectetur adipiscing elit, sed do eiusmod tempor incididunt ut labore et dolore magna aliqua. Ut enim ad minim veniam, quis nostrud exercitation ullamco laboris nisi ut aliquip ex ea commodo consequat. Duis aute irure dolor in reprehenderit in voluptate velit esse cillum dolore eu fugiat nulla pariatur.</p>
  <a class="hex outline" style="left:516px;top:1428px;width:168px"><span>Contact Us</span></a>
</section>

<div class="abs sketch-hops" role="img" aria-label="Sketch of a hop cluster"></div>

<!-- detroit style -->
<section>
  <div class="abs photo-pizza-pan" role="img" aria-label="Photo of a tomato and basil pizza in a baking pan"></div>
  <div class="abs photo-cans" role="img" aria-label="Photo of two colourful beer cans"></div>
  <div class="abs rule" style="left:625px;top:1626px"></div>
  <h2 class="abs section-title" style="left:625px;top:1634px;width:480px">What is Detroit-style pizza?</h2>
  <p class="abs body-copy" style="left:627px;top:1737px;width:480px">Lorem ipsum dolor sit amet, consectetur adipiscing elit, sed do eiusmod tempor incididunt ut labore et dolore magna aliqua. Ut enim ad minim veniam, quis nostrud exercitation ullamco laboris nisi ut aliquip ex ea commodo consequat.</p>
  <a class="hex solid" style="left:628px;top:1864px;width:170px"><span>View Full Menu</span></a>
  <a class="hex outline" style="left:824px;top:1864px;width:170px"><span>Order Delivery</span></a>
</section>

<!-- footer -->
<footer>
  <svg class="abs" style="left:0;top:2080px" width="1200" height="389" viewBox="0 2080 1200 389">
    <polygon points="0,2146 604,2094 640,2094 1200,2146 1200,2469 0,2469" fill="var(--footer)"/>
    <polygon points="0,2144 604,2083 604,2097 0,2158" fill="var(--red)"/>
    <polygon points="640,2083 1200,2144 1200,2158 640,2097" fill="var(--red)"/>
  </svg>
  <div class="abs footer-name">Lantern Hollow<br>Brewing Co.</div>
  <div class="abs footer-address">
    <div class="line">
      <svg width="14" height="18" viewBox="0 0 14 18"><path d="M7 0a7 7 0 0 0-7 7c0 5 7 11 7 11s7-6 7-11a7 7 0 0 0-7-7zm0 10a3 3 0 1 1 0-6 3 3 0 0 1 0 6z" fill="#fff"/></svg>
      <span>Lantern Hollow Brewing Company</span>
    </div>
    <div>48 Millrace Lane, Suite 2</div>
    <div>Portland, Maine 04199</div>
  </div>
  <div class="abs footer-phone">
    <svg width="18" height="18" viewBox="0 0 24 24"><path d="M6.6 10.8a15.1 15.1 0 0 0 6.6 6.6l2.2-2.2a1 1 0 0 1 1-.25 11.4 11.4 0 0 0 3.6.57 1 1 0 0 1 1 1V20a1 1 0 0 1-1 1A17 17 0 0 1 3 4a1 1 0 0 1 1-1h3.5a1 1 0 0 1 1 1c0 1.25.2 2.45.57 3.57a1 1 0 0 1-.25 1z" fill="#fff"/></svg>
    <span>++ (207) 555-0142</span>
  </div>
  <nav class="abs footer-nav">
    <a style="left:307px">The Kitchen</a>
    <a style="left:466px">Our Beers</a>
    <a style="left:607px">Visit Us</a>
    <a style="left:723px">About Us</a>
    <a style="left:857px">Merch</a>
  </nav>
  <div class="abs footer-rule"></div>
  <p class="abs copyright">© copyrights Lantern Hollow Brewing Company | &nbsp;All Rights Reserved</p>
  <div class="abs social"><span>Sociale media:</span><i></i><i></i><i></i><i></i></div>
</footer>

</body>
</html>
```